Voltaro Cycles Company

I need a Voltaro Cycles site for pre-orders, 3-4 models, multiple colors per order. The bikes are electric bikes, company logo color scheme has red. Maybe a countdown to a date when pre-order will close. I also want to incorporate a deposit style system for the pre-order with the balance due on shipping.

```html
<!DOCTYPE html>
<html lang="en">
<head>
<meta charset="UTF-8">
<title>Voltaro Cycles — Electric Bike Pre-Order</title>
<link rel="stylesheet" href="https://fonts.googleapis.com/css2?family=Audiowide&family=Arimo:wght@400;500;700&display=swap">
<style>
:root{
  --red:#c8102e;
  --pink:#f8e3e6;
  --pink-band:#ecd3d7;
  --grey:#eeeeee;
  --ink:#111111;
  --white:#ffffff;
  --black:#000000;
}
*{margin:0;padding:0;box-sizing:border-box}
html,body{width:1200px;height:4587px;overflow:hidden}
body{position:relative;background:var(--white);font-family:'Arimo',Arial,sans-serif;color:var(--ink)}
.abs{position:absolute}
.display{font-family:'Audiowide',Arial,sans-serif;font-weight:400}

/* header */
.site-header{left:0;top:0;width:1200px;height:72px;background:var(--white)}
.brand{left:110px;top:23px;font-family:'Arimo',Arial,sans-serif;font-weight:500;font-size:23px;color:#222;white-space:nowrap}
.nav a{position:absolute;top:30px;font-family:'Audiowide',sans-serif;font-size:13px;color:#222;text-decoration:none;white-space:nowrap}
.nav a.active{color:var(--red)}
.btn-preorder{left:918px;top:12px;width:170px;height:46px;background:var(--red);color:#fff;border-radius:6px;font-family:'Audiowide',sans-serif;font-size:20px;text-align:center;line-height:44px}

/* hero */
.hero{left:0;top:72px;width:1200px;height:513px;background:var(--grey);overflow:hidden}
.hero-stripe{left:0;top:0}
.hero-bike{left:95px;top:50px;width:610px;height:410px;border-radius:30px;background:radial-gradient(ellipse at 55% 50%,#b8ae9c 0%,#9a8e7c 35%,rgba(120,108,94,.5) 60%,rgba(238,238,238,0) 75%)}
.hero-title{left:738px;top:84px;font-size:33px;line-height:53px;color:#111;white-space:nowrap}
.hero-title .accent{color:var(--red)}
.countdown .ghost{position:absolute;font-family:'Audiowide',sans-serif;font-size:18px;color:#9a9a9a}
.countdown .digit{position:absolute;top:311px;width:52px;height:50px;background:var(--red);color:#fff;border-radius:6px;font-family:'Audiowide',sans-serif;font-size:22px;text-align:center;line-height:50px}
.countdown .sep{position:absolute;top:318px;font-size:26px;color:#333}

.section-title{left:0;width:1200px;text-align:center;font-family:'Audiowide',sans-serif;font-weight:400;font-size:37px;color:var(--red)}

/* featured */
.feature-card{top:770px;width:478px;height:282px;border-radius:14px;overflow:hidden}
.feature-card .photo{position:absolute;inset:0}
.feature-card h3{position:absolute;top:45px;font-family:'Audiowide',sans-serif;font-weight:400;font-size:25px;color:#fff;white-space:nowrap}
.feature-card p{position:absolute;top:100px;width:240px;font-size:14px;line-height:28px;color:#fff}
.feature-card .btn-light{position:absolute;top:176px;width:170px;height:45px;background:#fff;color:#111;border-radius:6px;font-family:'Audiowide',sans-serif;font-size:18px;text-align:center;line-height:45px}
.dots span{position:absolute;top:1095px;width:28px;height:5px;border-radius:3px;background:#e69aa6}
.dots span.on{background:var(--red)}

/* about */
.about{left:0;top:1190px;width:1200px;height:515px;overflow:hidden;background:linear-gradient(180deg,#7b8a96 0%,#4f5a57 35%,#3c3f39 70%,#2f3030 100%)}
.about-rider{left:520px;top:0;width:420px;height:515px;background:linear-gradient(180deg,rgba(190,190,200,.35),rgba(200,60,60,.25) 70%,rgba(30,30,30,.2))}
.about-veil{left:0;top:0}
.about h2{left:108px;top:98px;font-family:'Audiowide',sans-serif;font-weight:400;font-size:37px;color:#fff}
.about p{left:108px;top:170px;width:455px;font-size:16px;line-height:34.5px;color:#fff;font-weight:500}
.btn-white{left:108px;top:368px;width:170px;height:45px;background:#fff;border-radius:5px;font-family:'Audiowide',sans-serif;font-size:18px;line-height:45px;text-align:center;color:#111}

/* news */
.news{top:1887px;width:313px}
.news .photo{width:313px;height:231px;border-radius:12px}
.news .date{margin-top:42px;font-family:'Audiowide',sans-serif;font-size:16px;color:var(--red)}
.news p{margin-top:18px;font-size:13.4px;line-height:32px;text-align:justify;color:#111}
.news .btn-red{margin-top:22px;width:150px;height:40px;background:var(--red);color:#fff;border-radius:5px;font-family:'Audiowide',sans-serif;font-size:16px;line-height:40px;text-align:center}

/* video */
.video{left:0;top:2442px;width:1200px;height:433px;background:linear-gradient(100deg,#e8b25a 0%,#a86a2c 25%,#3d3a35 45%,#2c3235 60%,#5a6a3c 80%,#c59a4c 100%)}
.video-veil{left:0;top:2442px}
.play{left:572px;top:2630px}

/* products */
.product{top:3045px;width:314px;height:318px;background:#fff;border-radius:14px;box-shadow:0 0 10px rgba(0,0,0,.18)}
.product .photo{position:absolute;left:22px;top:40px;width:270px;height:235px;border-radius:10px}
.swatches{top:3396px;width:314px;display:flex;justify-content:center;gap:17px}
.swatches i{display:block;width:35px;height:35px;border-radius:50%}
.product-name{top:3447px;width:314px;text-align:center;font-family:'Audiowide',sans-serif;font-size:20px;color:var(--red)}
.product-price{top:3490px;width:314px;text-align:center;font-family:'Audiowide',sans-serif;font-size:18px;color:#111}
.arrow{top:3264px}

/* contact */
.map{left:111px;top:3688px;width:465px;height:450px;border-radius:10px;background:linear-gradient(150deg,#4a4a4a,#3a3b3d 60%,#444a44)}
.field{left:600px;width:488px;height:66px;background:var(--pink);border-radius:10px;font-family:'Audiowide',sans-serif;font-size:16px;color:#111;padding:25px 0 0 28px}
.btn-send{left:770px;top:4083px;width:148px;height:40px;background:var(--red);color:#fff;border-radius:5px;font-family:'Audiowide',sans-serif;font-size:18px;line-height:40px;text-align:center}

/* footer */
.site-footer{left:0;top:4225px;width:1200px;height:362px;background:var(--black);color:#fff}
.footer-brand{top:48px;width:1200px;text-align:center;font-family:'Arimo',Arial,sans-serif;font-weight:500;font-size:23px}
.footer-nav a{position:absolute;top:120px;font-size:15px;font-weight:500;color:#fff;text-decoration:none;white-space:nowrap}
.contact-item .icon{position:absolute;top:190px}
.contact-item h4{position:absolute;top:187px;font-family:'Audiowide',sans-serif;font-size:22px;color:var(--red);font-weight:400}
.contact-item span{position:absolute;top:237px;font-size:16px;color:#fff;white-space:nowrap}
.copyright{top:302px;width:1200px;text-align:center;font-size:16px;font-weight:500}
</style>
</head>
<body>

<header class="site-header abs">
  <div class="brand abs">Voltaro Cycles</div>
  <nav class="nav">
    <a class="active" style="left:335px">HOME</a>
    <a style="left:422px">ABOUT US</a>
    <a style="left:548px">FEATURED SELL</a>
    <a style="left:728px">LATEST NEWS</a>
  </nav>
  <div class="btn-preorder abs">pre-order</div>
</header>

<section class="hero abs">
  <svg class="hero-stripe abs" width="1200" height="513"><polygon points="410,0 650,0 392,513 157,513" fill="var(--pink-band)"/></svg>
  <div class="hero-bike abs" role="img" aria-label="Photo of a bronze step-through electric bicycle"></div>
  <h1 class="hero-title abs display">Reserve the product<br>with intial payment<br>of <span class="accent">10%</span></h1>
  <div class="countdown">
    <span class="ghost" style="left:750px;top:268px">07</span>
    <span class="ghost" style="left:872px;top:268px">19</span>
    <span class="ghost" style="left:997px;top:268px">00</span>
    <span class="digit" style="left:740px">08</span>
    <span class="sep" style="left:822px">:</span>
    <span class="digit" style="left:862px">20</span>
    <span class="sep" style="left:944px">:</span>
    <span class="digit" style="left:985px">01</span>
    <span class="ghost" style="left:750px;top:388px">09</span>
    <span class="ghost" style="left:872px;top:388px">21</span>
    <span class="ghost" style="left:997px;top:388px">02</span>
  </div>
</section>

<h2 class="section-title abs" style="top:662px">Featured Sell</h2>

<article class="feature-card abs" style="left:112px">
  <div class="photo" role="img" aria-label="Man in a suit sitting on an electric bike with a coffee, red overlay" style="background:linear-gradient(90deg,#c8102e 0%,#c8102e 40%,#b65060 65%,#a8a2a0 100%)"></div>
  <h3 style="left:24px">Electric Bicycles</h3>
  <p style="left:24px">Sed ut perspiciatis unde omnis iste natus error sit voluptatem</p>
  <div class="btn-light" style="left:26px">View Details</div>
</article>
<article class="feature-card abs" style="left:610px">
  <div class="photo" role="img" aria-label="Rider on an electric mountain bike outdoors, red overlay" style="background:linear-gradient(270deg,#c8102e 0%,#c8102e 40%,#b34d62 65%,#5d6e6a 100%)"></div>
  <h3 style="right:24px">Electric Bicycles</h3>
  <p style="left:210px;width:240px">Sed ut perspiciatis unde omnis iste natus error sit voluptatem</p>
  <div class="btn-light" style="left:271px">View Details</div>
</article>
<div class="dots"><span class="on" style="left:548px"></span><span style="left:586px"></span><span style="left:624px"></span></div>

<section class="about abs">
  <div class="about-rider abs" role="img" aria-label="Smiling woman riding an electric bike on a country road"></div>
  <svg class="about-veil abs" width="1200" height="515"><polygon points="0,0 560,0 360,515 0,515" fill="rgba(60,60,60,.45)"/><polygon points="860,0 1200,0 1200,515 650,515" fill="rgba(200,16,46,.18)"/></svg>
  <h2 class="abs">About Us</h2>
  <p class="abs">Nemo enim ipsam voluptatem quia voluptas sit aspernatur aut odit aut fugit, sed quia consequuntur magni dolores eos qui ratione voluptatem sequi nesciunt. Neque porro quisquam est, qui dolorem ipsum quia dolor sit amet, consectetur.</p>
  <div class="btn-white abs">Learn More</div>
</section>

<h2 class="section-title abs" style="top:1780px">Latest News</h2>

<article class="news abs" style="left:111px">
  <div class="photo" role="img" aria-label="Electric bike close-up at sunset" style="background:linear-gradient(160deg,#8fb1cf,#6c6a5a 55%,#3b3428)"></div>
  <div class="date">06th April 2023</div>
  <p>Neque porro quisquam est, qui dolorem ipsum quia dolor sit amet, consectetur, adipisci velit, sed quia non numquam eius modi tempora</p>
  <div class="btn-red">Read More</div>
</article>
<article class="news abs" style="left:443px">
  <div class="photo" role="img" aria-label="Woman at a row of red shared city bikes" style="background:linear-gradient(160deg,#c9d4df,#9a9aa8 45%,#b03040 80%,#8a8a8a)"></div>
  <div class="date">06th May 2023</div>
  <p>Neque porro quisquam est, qui dolorem ipsum quia dolor sit amet, consectetur, adipisci velit, sed quia non numquam eius modi tempora</p>
  <div class="btn-red">Read More</div>
</article>
<article class="news abs" style="left:775px">
  <div class="photo" role="img" aria-label="Parked electric bikes on a street at golden hour" style="background:linear-gradient(160deg,#6d7580,#d9a654 50%,#4a4038)"></div>
  <div class="date">06th June 2023</div>
  <p>Neque porro quisquam est, qui dolorem ipsum quia dolor sit amet, consectetur, adipisci velit, sed quia non numquam eius modi tempora</p>
  <div class="btn-red">Read More</div>
</article>

<section class="video abs" role="img" aria-label="Video still: e-bike handlebar at sunset on a country road"></section>
<svg class="video-veil abs" width="1200" height="433"><polygon points="520,0 650,0 380,433 250,433" fill="rgba(200,16,46,.18)"/></svg>
<svg class="play abs" width="56" height="56" viewBox="0 0 56 56"><circle cx="28" cy="28" r="28" fill="var(--red)"/><polygon points="22,17 40,28 22,39" fill="#fff"/></svg>

<h2 class="section-title abs" style="top:2946px">Our Products</h2>

<svg class="arrow abs" style="left:45px" width="42" height="42"><circle cx="21" cy="21" r="21" fill="var(--red)"/><polyline points="24,13 16,21 24,29" fill="none" stroke="#fff" stroke-width="2.5"/></svg>
<svg class="arrow abs" style="left:1111px" width="42" height="42"><circle cx="21" cy="21" r="21" fill="var(--red)"/><polyline points="18,13 26,21 18,29" fill="none" stroke="#fff" stroke-width="2.5"/></svg>

<div class="product abs" style="left:110px"><div class="photo" role="img" aria-label="Black electric trekking bike" style="background:radial-gradient(ellipse,#bdbdbd 0%,#f6f6f6 65%,#fff 100%)"></div></div>
<div class="product abs" style="left:440px"><div class="photo" role="img" aria-label="Silver step-through electric city bike" style="background:radial-gradient(ellipse,#d2d2d2 0%,#f6f6f6 65%,#fff 100%)"></div></div>
<div class="product abs" style="left:773px"><div class="photo" role="img" aria-label="Blue electric mountain bike" style="background:radial-gradient(ellipse,#9aa4d4 0%,#f2f3f8 65%,#fff 100%)"></div></div>

<div class="swatches abs" style="left:110px"><i style="background:#4d4f55"></i><i style="background:#c8102e"></i><i style="background:#0dab3e"></i></div>
<div class="swatches abs" style="left:440px"><i style="background:#bdbdbd"></i><i style="background:#c21ac2"></i><i style="background:#12a6c8"></i></div>
<div class="swatches abs" style="left:773px"><i style="background:#1430c8"></i><i style="background:#c6b215"></i><i style="background:#050505"></i></div>

<div class="product-name abs" style="left:110px">Lorem Lipsum</div>
<div class="product-name abs" style="left:440px">Lorem Lipsum</div>
<div class="product-name abs" style="left:773px">Lorem Lipsum</div>
<div class="product-price abs" style="left:110px">$34.98</div>
<div class="product-price abs" style="left:440px">$56.32</div>
<div class="product-price abs" style="left:773px">$89.22</div>

<h2 class="section-title abs" style="top:3582px">Contact Us</h2>

<div class="map abs" role="img" aria-label="Street map showing the store location"></div>
<div class="field abs" style="top:3697px">Full Name</div>
<div class="field abs" style="top:3777px">Email Address</div>
<div class="field abs" style="top:3858px">Mobile Number</div>
<div class="field abs" style="top:3938px;height:120px">Message</div>
<div class="btn-send abs">Send Now</div>

<footer class="site-footer abs">
  <div class="footer-brand abs">Voltaro Cycles</div>
  <nav class="footer-nav">
    <a style="left:279px">HOME</a>
    <a style="left:368px">ABOUT US</a>
    <a style="left:492px">FEATURED SELL</a>
    <a style="left:663px">LATEST NEWS</a>
    <a style="left:818px">CONTACT US</a>
  </nav>
  <div class="contact-item">
    <svg class="icon" style="left:113px" width="48" height="48" viewBox="0 0 48 48"><circle cx="24" cy="24" r="24" fill="var(--red)"/><path d="M17 13c1-1 2-1 3 0l3 4c.6.8.5 1.8-.2 2.5l-1.6 1.6c1 2.4 3 4.4 5.4 5.4l1.6-1.6c.7-.7 1.7-.8 2.5-.2l4 3c1 1 1 2 0 3l-2 2c-6 1-17-10-16-16z" fill="#fff"/></svg>
    <h4 style="left:199px">CALL US:</h4>
    <span style="left:199px;font-size:14px">+1 999 999 9999</span>
  </div>
  <div class="contact-item">
    <svg class="icon" style="left:445px" width="48" height="48" viewBox="0 0 48 48"><circle cx="24" cy="24" r="24" fill="var(--red)"/><rect x="13" y="16" width="22" height="16" rx="2" fill="#fff"/><polyline points="13,17 24,26 35,17" fill="none" stroke="var(--red)" stroke-width="2"/></svg>
    <h4 style="left:523px">MAIL US:</h4>
    <span style="left:523px">orders@voltarocycles.shop</span>
  </div>
  <div class="contact-item">
    <svg class="icon" style="left:846px" width="48" height="48" viewBox="0 0 48 48"><circle cx="24" cy="24" r="24" fill="var(--red)"/><path d="M24 12a8 8 0 0 0-8 8c0 6 8 15 8 15s8-9 8-15a8 8 0 0 0-8-8z" fill="#fff"/><circle cx="24" cy="20" r="3" fill="var(--red)"/></svg>
    <h4 style="left:926px">REACH US:</h4>
    <span style="left:926px">54, Lorem Lipsum</span>
  </div>
  <div class="copyright abs">@2023 Copyrights. Voltaro Cycles. All Rights Reserved.</div>
</footer>

</body>
</html>
```